National Mission Critical Construction Contractor needs Stationery Design to make a bold statement

We are a small commercial construction company, working primarily in mission critical facilities across the U.S.. We have exciting corporate changes going an and a new logo and office space so we need new stationery. The final design should incorporate our new logo and invoke a fresh, high-tech feel while looking simple and modern.

Industry/Entity Type

Construction

Contact Information for Business Card

We are required to list our state licensing qualifications on the back of our card.

Font styles to use
Sans Serif

Requirements
Must have
• We need to have a design for second page of stationery, envelopes both standard and with a window and for a 3 x 4 notepad.

```html
<!DOCTYPE html>
<html lang="en">
<head>
<meta charset="utf-8">
<title>Ridgeway Construction Management – Stationery</title>
<link href="https://fonts.googleapis.com/css2?family=Source+Sans+3:wght@400;600&family=Exo+2:wght@600&display=swap" rel="stylesheet">
<style>
:root{
  --stage:#a9a8a9;
  --paper:#f4f3f1;
  --card:#ffffff;
  --blue:#0e72bb;
  --blue-mid:#2f9fdc;
  --blue-light:#4fb0de;
  --green:#8bc53f;
  --ink:#444;
}
*{box-sizing:border-box;margin:0;padding:0}
html,body{width:1160px;height:1200px;overflow:hidden;background:var(--stage)}
body{position:relative;font-family:"Source Sans 3",sans-serif;color:var(--ink)}
.piece{position:absolute;background:var(--paper);box-shadow:2px 3px 6px rgba(0,0,0,.28);overflow:hidden}
.brand{position:absolute;text-align:center;color:var(--blue);font-family:"Source Sans 3",sans-serif;font-weight:600;letter-spacing:.04em;line-height:1}
.brand .name{display:block;border-bottom:1px solid #c9ccd1;padding-bottom:2px}
.brand .sub{display:block;font-weight:400;letter-spacing:.22em;margin-top:3px}
.brand .dot{display:inline-block;border-radius:50%;border:2px solid currentColor;vertical-align:middle}

/* decorative colour fields */
.band-bottom{position:absolute;left:0;bottom:0;width:100%;background:linear-gradient(180deg,var(--blue-light) 0%,var(--blue) 55%)}
.band-side{position:absolute;left:0;top:0;height:100%;background:linear-gradient(90deg,var(--blue) 55%,var(--blue-light) 100%)}

/* letterhead */
.letterhead{left:70px;top:71px;width:473px;height:667px}
.letterhead .brand{left:46px;top:108px;width:112px}
.letterhead .brand .name{font-size:15px}
.letterhead .brand .sub{font-size:4px;letter-spacing:.14em}
.letterhead .band-bottom{height:70px}
.contact{position:absolute;left:332px;top:44px;font-size:7.5px;line-height:10.6px}
.contact ul{list-style:none;margin-top:4px}
.contact li{display:flex;align-items:center;gap:4px}
.contact svg{width:6px;height:6px;fill:var(--blue)}
.letter{position:absolute;left:47px;top:188px;width:380px}
.letter .greeting{font-size:12.5px;margin-bottom:24px}
.letter p{font-size:6.6px;line-height:11.3px;margin-bottom:11px;text-align:justify;font-weight:400}
.letter .signoff{margin-top:22px}
.letter .sig{display:block;width:60px;height:18px;margin:4px 0 10px}
.letter .signer{font-size:7.5px;line-height:12.5px;padding-left:2px}

/* folder */
.folder{left:580px;top:38px;width:503px;height:709px}
.folder .band-side{width:64px}
.folder .brand{left:207px;top:130px;width:236px}
.folder .brand .name{font-size:40px;letter-spacing:.02em;padding-bottom:4px;border-bottom-width:2px}
.folder .brand .sub{font-size:9.5px;letter-spacing:.26em;margin-top:5px}
.folder .brand .dot{width:24px;height:24px;margin-bottom:6px}
.folder h1{position:absolute;left:192px;top:470px;font-family:"Exo 2",sans-serif;font-weight:600;font-size:28px;color:var(--blue);white-space:nowrap}

/* envelopes */
.envelope-back{left:154px;top:802px;width:530px;height:242px;background:#fff}
.flap{position:absolute;left:0;top:0}
.flap-url{position:absolute;left:0;width:100%;top:61px;text-align:center;color:#fff;font-size:7.5px}
.envelope-front{left:87px;top:910px;width:531px;height:243px}
.envelope-front .brand{left:24px;top:55px;width:114px}
.envelope-front .brand .name{font-size:15px}
.envelope-front .brand .sub{font-size:4px;letter-spacing:.14em}
.envelope-front address{position:absolute;left:44px;top:95px;font-style:normal;font-size:7.8px;line-height:11px;text-align:center}
.envelope-front .band-bottom{height:50px}

/* business cards */
.card{position:absolute;left:758px;width:318px;height:181px;border-radius:10px;overflow:hidden;box-shadow:1px 2px 4px rgba(0,0,0,.25)}
.card-front{top:780px;background:var(--card)}
.card-front .brand{left:82px;top:35px;width:154px}
.card-front .brand .name{font-size:19px}
.card-front .brand .sub{font-size:5.6px;letter-spacing:.2em}
.band{position:absolute;left:0;top:103px;width:100%;height:67px;background:linear-gradient(90deg,var(--blue) 0 50%,var(--blue-mid) 50% 100%)}
.band .ring{position:absolute;left:125px;top:-2px;width:70px;height:70px;border-radius:50%;border:3px solid #fff;background:linear-gradient(90deg,var(--blue) 0 50%,var(--blue-mid) 50% 100%)}
.person{position:absolute;left:13px;top:9px;color:#fff;font-size:8.2px;line-height:12.5px}
.person strong{display:block;font-size:11.5px;font-weight:600;letter-spacing:.02em}
.card-contact{position:absolute;right:14px;top:11px;list-style:none;color:#fff;font-size:8px;line-height:12.2px;text-align:right}
.card-contact li{display:flex;justify-content:flex-end;align-items:center;gap:4px}
.card-contact svg{width:7px;height:7px;fill:#fff}
.card-back{top:974px;background:var(--blue)}
.card-back .brand{left:91px;top:68px;width:136px;color:#fff}
.card-back .brand .name{font-size:18px;border-color:#fff}
.card-back .brand .sub{font-size:5.4px;letter-spacing:.2em}
.card-back .brand .dot{width:30px;height:30px;margin-bottom:8px}
</style>
</head>
<body>

<!-- Letterhead -->
<section class="piece letterhead">
  <div class="brand"><span class="name">RIDGEWAY</span><span class="sub">CONSTRUCTION MANAGEMENT</span></div>
  <div class="contact">
    214 Alder Street<br>Fairbanks, Alaska 99701
    <ul>
      <li><svg viewBox="0 0 10 10"><path d="M2 0h2l1 3-1.5 1a6 6 0 0 0 2.5 2.5L7 5l3 1v2c0 1-1 2-2 2C4 10 0 6 0 2c0-1 1-2 2-2z"/></svg>555 210 4471</li>
      <li><svg viewBox="0 0 10 10"><path d="M2.5 0h5v10h-5zM3.5 1v7h3V1z"/></svg>555 318 2096</li>
      <li><svg viewBox="0 0 10 10"><path d="M2 0h6v3H2zM0 4h10v4H8v2H2V8H0z"/></svg>555 742 6630</li>
      <li><svg viewBox="0 0 10 10"><path d="M0 2h10v6H0z"/></svg>hello@ridgewaycm.com</li>
      <li><svg viewBox="0 0 10 10"><circle cx="5" cy="5" r="5"/></svg>www.ridgewaycm.com</li>
    </ul>
  </div>
  <div class="letter">
    <p class="greeting">Dear Mr. Reyes,</p>
    <p>Lorem ipsum dolor sit amet, consectetur adipiscing elit. Donec orci purus, luctus vitae dignissim eu, iaculis sed purus. Vivamus faucibus, ipsum nec aliquet viverra, leo mauris condimentum ligula, sit amet sagittis enim ligula quis arcu. Nam egestas tortor id nisi porttitor mattis. In tortor ante, ultricies in suscipit a, tempus non massa. Vivamus et auctor mi. Fusce vel massa nulla. Phasellus nec eros mauris, et scelerisque orci.</p>
    <p>Donec malesuada orci vitae nulla accumsan porta a id massa. Quisque accumsan iaculis magna sit amet fringilla. Maecenas consequat, magna eget tincidunt semper, odio nibh rutrum mi, id feugiat ante nisi eu risus. Vestibulum nunc orci, rhoncus a placerat in, ultricies in mi. Cras mattis varius eros, vel fringilla nisi suscipit eget. Quisque scelerisque sagittis nulla at porttitor.</p>
    <p>Sed id augue vitae urna euismod commodo aliquet a quam. Pellentesque arcu velit, cursus et malesuada ut, consequat et diam. Nullam erat sem, rhoncus id ullamcorper vitae, rhoncus et arcu. In ultricies ultricies nulla, ut rutrum nisi iaculis at. Donec eu magna a metus ornare faucibus. Fusce aliquet faucibus ultricies. Morbi semper, est id tincidunt gravida, sem arcu adipiscing lacus, ac bibendum nulla leo eu purus. Quisque nec diam sed risus consectetur a cursus quis nibh. Vestibulum id purus lorem.</p>
    <p>It is a long established fact that a reader will be distracted by the readable content of a page when looking at its layout. The point of using Lorem Ipsum is that it has a more-or-less normal distribution of letters, as opposed to using 'Content here, content here', making it look like readable English. Many desktop publishing packages</p>
    <p class="signoff">Sincerely,</p>
    <svg class="sig" viewBox="0 0 60 18" fill="none" stroke="#222" stroke-width=".8"><path d="M0 10c15-2 30-2 50-1M32 2c-4 4-3 10 1 14M34 9c6 1 12 2 20 1"/></svg>
    <div class="signer">Daniel Reyes<br>CEO/ Founder</div>
  </div>
  <div class="band-bottom" role="img" aria-label="Decorative blue and green colour band along the foot of the page"></div>
</section>

<!-- Presentation folder -->
<section class="piece folder">
  <div class="band-side" role="img" aria-label="Decorative blue and green colour band along the left edge"></div>
  <div class="brand"><span class="dot"></span><br><span class="name">RIDGEWAY</span><span class="sub">CONSTRUCTION MANAGEMENT</span></div>
  <h1>Project Cover Sheet</h1>
</section>

<!-- Envelope, back -->
<section class="piece envelope-back">
  <svg class="flap" width="530" height="90" viewBox="0 0 530 90">
    <path fill="var(--blue)" d="M0 0H530L518 62Q512 88 486 88H44Q18 88 12 62Z"/>
  </svg>
  <div class="flap-url">www.ridgewaycm.com</div>
</section>

<!-- Envelope, front -->
<section class="piece envelope-front">
  <div class="brand"><span class="name">RIDGEWAY</span><span class="sub">CONSTRUCTION MANAGEMENT</span></div>
  <address>214 Alder Street<br>Fairbanks, Alaska 99701</address>
  <div class="band-bottom" role="img" aria-label="Decorative blue and green colour band along the foot of the envelope"></div>
</section>

<!-- Business card, front -->
<section class="card card-front">
  <div class="brand"><span class="name">RIDGEWAY</span><span class="sub">CONSTRUCTION MANAGEMENT</span></div>
  <div class="band">
    <div class="person"><strong>DANIEL REYES</strong>CEO/Founder<br>214 Alder Street<br>Fairbanks, Alaska 99701</div>
    <div class="ring"></div>
    <ul class="card-contact">
      <li>555 210 4471<svg viewBox="0 0 10 10"><path d="M2 0h2l1 3-1.5 1a6 6 0 0 0 2.5 2.5L7 5l3 1v2c0 1-1 2-2 2C4 10 0 6 0 2c0-1 1-2 2-2z"/></svg></li>
      <li>555 318 2096<svg viewBox="0 0 10 10"><path d="M2.5 0h5v10h-5zM3.5 1v7h3V1z"/></svg></li>
      <li>555 742 6630<svg viewBox="0 0 10 10"><path d="M2 0h6v3H2zM0 4h10v4H8v2H2V8H0z"/></svg></li>
      <li>hello@ridgewaycm.com<svg viewBox="0 0 10 10"><path d="M0 2h10v6H0z"/></svg></li>
    </ul>
  </div>
</section>

<!-- Business card, back -->
<section class="card card-back">
  <div class="brand"><span class="dot"></span><br><span class="name">RIDGEWAY</span><span class="sub">CONSTRUCTION MANAGEMENT</span></div>
</section>

</body>
</html>
```